Venture 482 - Lumora Book Cover

I am looking for a Lumora book cover for my book about "Venture 482".
The Book is Titled:
Venture 482 Ascended
Shaping Outcomes: Paths To Unlocking Cosmic Truths
Author is Dorian Pell
Here is a book description that may help you understand more about it:
Inspired by the genius of Edwin Marlowe, this comprehensive guide delves into the ancient wisdom and cutting-edge science behind the 482 method, a powerful tool for manifesting your desires. Whether you're seeking personal growth, financial success, or spiritual enlightenment, this book provides advanced techniques and methods to transform your dreams into reality.
Any questions please ask.
Thanks
Owen

```html
<!DOCTYPE html>
<html lang="en">
<head>
<meta charset="utf-8">
<title>Venture 482 Ascended — Dorian Pell</title>
<link rel="stylesheet" href="https://fonts.googleapis.com/css2?family=Bebas+Neue&family=Oswald:wght@200;300;600&family=Poppins:wght@500&display=swap">
<style>
  :root {
    --ink: #2b3a7a;
    --ink-soft: #3a4a8c;
    --paper-light: #e6e6e8;
    --paper-mid: #d2d2d5;
    --paper-edge: #bdbdc0;
    --emblem-core: #e9e9f0;
    --emblem-ring: #5a63a6;
  }
  * { margin: 0; padding: 0; box-sizing: border-box; }
  html, body { width: 805px; height: 1200px; overflow: hidden; }
  body { background: var(--paper-mid); }
  .cover {
    position: relative;
    width: 805px;
    height: 1200px;
    overflow: hidden;
    background:
      radial-gradient(ellipse 70% 55% at 50% 8%, var(--paper-light) 0%, rgba(230,230,232,0) 70%),
      linear-gradient(180deg, var(--paper-light) 0%, var(--paper-mid) 55%, var(--paper-edge) 100%);
    color: var(--ink);
  }
  .title-word {
    position: absolute;
    left: 0;
    width: 805px;
    text-align: center;
    font-family: "Bebas Neue", "Arial Narrow", sans-serif;
    font-size: 196px;
    line-height: 1;
    letter-spacing: 2px;
    color: var(--ink);
    transform: scaleX(0.74);
    transform-origin: 50% 50%;
  }
  .title-top { top: 8px; }
  .title-bottom { top: 690px; }
  .emblem {
    position: absolute;
    left: 112px;
    top: 200px;
    width: 580px;
    height: 580px;
  }
  .emblem-number {
    position: absolute;
    left: 0;
    top: 430px;
    width: 805px;
    text-align: center;
    font-family: "Poppins", "Helvetica", sans-serif;
    font-weight: 500;
    font-size: 100px;
    line-height: 1;
    letter-spacing: -2px;
    color: var(--ink);
  }
  .subtitle {
    position: absolute;
    left: 0;
    top: 884px;
    width: 805px;
    text-align: center;
    font-family: "Oswald", "Arial Narrow", sans-serif;
    text-transform: uppercase;
    color: var(--ink);
  }
  .subtitle-lead {
    display: block;
    font-weight: 600;
    font-size: 22px;
    line-height: 26px;
  }
  .subtitle-rest {
    display: block;
    font-weight: 300;
    font-size: 20px;
    line-height: 27px;
    color: var(--ink-soft);
  }
  .author {
    position: absolute;
    left: 0;
    top: 1030px;
    width: 805px;
    text-align: center;
    font-family: "Oswald", "Arial Narrow", sans-serif;
    font-weight: 200;
    font-size: 124px;
    line-height: 1.1;
    letter-spacing: 16px;
    padding-left: 16px;
    text-transform: uppercase;
    color: var(--ink);
  }
</style>
</head>
<body>
  <main class="cover">
    <h1 class="title">
      <span class="title-word title-top">Venture</span>
      <span class="title-word title-bottom">Ascended</span>
    </h1>

    <svg class="emblem" viewBox="0 0 580 580" role="img" aria-label="Sacred geometry mandala emblem with radiating rays, in navy and violet ink">
      <defs>
        <radialGradient id="emblem-fill" cx="50%" cy="50%" r="50%">
          <stop offset="0%" stop-color="var(--emblem-core)"/>
          <stop offset="45%" stop-color="#c9cbe0"/>
          <stop offset="70%" stop-color="var(--emblem-ring)"/>
          <stop offset="78%" stop-color="var(--ink)"/>
          <stop offset="100%" stop-color="rgba(43,58,122,0)"/>
        </radialGradient>
      </defs>
      <circle cx="290" cy="290" r="288" fill="url(#emblem-fill)"/>
    </svg>
    <div class="emblem-number">482</div>

    <p class="subtitle">
      <span class="subtitle-lead">Shaping Outcomes:</span>
      <span class="subtitle-rest">Paths To Unlocking</span>
      <span class="subtitle-rest">Cosmic Truths</span>
    </p>

    <p class="author">Dorian Pell</p>
  </main>
</body>
</html>
```